Business Card Design

Business sales of reconditioned / used batteries with mobile delivery and install services. Customers base majority are auto car sales lots and individuals.

Card need to convey quality product reliability and quick prompt professional service.

Card must reflect excellence in customer care and product being offered

Target Market(s)

Auto car lots new and used. Auto repair shops. Individuals.

Industry/Entity Type

Business

Contact Information for Business Card

Batteries Q-Swift
Cars, Trucks, Boats, Motorcycles, lawn mowers, power tools
Delivery & install available most vehicles
Mon-Sat 9-6pm
Dale Morrick 501-738-2054
*product warranty 6 month shelf life battery/1 year blems battery

```html
<!DOCTYPE html>
<html lang="en">
<head>
<meta charset="utf-8">
<title>Batteries Q-Swift – Business Card</title>
<link rel="stylesheet" href="https://fonts.googleapis.com/css2?family=Open+Sans:wght@400;700;800&display=swap">
<style>
  :root {
    --page: #ffffff;
    --ink: #111111;
    --card-dark: #000000;
    --brand-red: #e30613;
    --text-light: #ffffff;
  }
  * { box-sizing: border-box; margin: 0; padding: 0; }
  html, body { width: 1200px; height: 1000px; overflow: hidden; background: var(--page); }
  body { position: relative; font-family: "Open Sans", Arial, sans-serif; }

  .card {
    position: absolute; left: 47px; top: 207px; width: 1086px; height: 638px;
    background: var(--page);
    box-shadow: 4px 6px 10px rgba(0,0,0,0.35);
    overflow: hidden;
  }
  .card__header { position: absolute; left: 0; top: 0; width: 100%; height: 228px; background: var(--page); }
  .brand {
    position: absolute; left: 150px; top: 78px;
    display: flex; align-items: center; gap: 18px;
    font-weight: 800; font-size: 66px; letter-spacing: -1px; color: var(--ink);
    line-height: 1;
  }
  .brand__mark { width: 34px; height: 34px; background: var(--brand-red); }
  .accent-band {
    position: absolute; left: 140px; top: 203px; width: 946px; height: 25px;
    background: linear-gradient(90deg, rgba(227,6,19,0) 0%, rgba(238,120,90,0.7) 35%, var(--brand-red) 85%, var(--brand-red) 100%);
  }
  .card__body { position: absolute; left: 0; top: 228px; width: 100%; height: 410px; background: var(--card-dark); color: var(--text-light); }

  .services { position: absolute; left: 60px; top: 16px; list-style: none; }
  .services li {
    display: flex; align-items: center; height: 42.6px;
    font-size: 33px; font-weight: 400;
  }
  .services svg { width: 26px; height: 26px; margin-right: 13px; flex: none; }

  .warranty { position: absolute; left: 58px; top: 330px; font-size: 25px; }

  .contact { position: absolute; right: 60px; top: 70px; text-align: right; }
  .contact__name { font-size: 42px; font-weight: 400; letter-spacing: 0.5px; line-height: 1.1; }
  .contact__phone { font-size: 56px; font-weight: 700; line-height: 1.1; }
  .contact__hours { font-size: 34px; font-weight: 400; margin-top: 40px; }
</style>
</head>
<body>
  <div class="card">
    <header class="card__header">
      <div class="brand"><span>BATTERIES Q-SWIFT</span><span class="brand__mark"></span></div>
      <div class="accent-band"></div>
    </header>
    <section class="card__body">
      <ul class="services">
        <li><svg viewBox="0 0 26 26"><path d="M1 3h7l8 10-8 10H1l8-10z M11 3h7l8 10-8 10h-7l8-10z" fill="#e30613"/></svg>Trucks</li>
        <li><svg viewBox="0 0 26 26"><path d="M1 3h7l8 10-8 10H1l8-10z M11 3h7l8 10-8 10h-7l8-10z" fill="#e30613"/></svg>Boats</li>
        <li><svg viewBox="0 0 26 26"><path d="M1 3h7l8 10-8 10H1l8-10z M11 3h7l8 10-8 10h-7l8-10z" fill="#e30613"/></svg>Motorcycles</li>
        <li><svg viewBox="0 0 26 26"><path d="M1 3h7l8 10-8 10H1l8-10z M11 3h7l8 10-8 10h-7l8-10z" fill="#e30613"/></svg>Lawn mowers</li>
        <li><svg viewBox="0 0 26 26"><path d="M1 3h7l8 10-8 10H1l8-10z M11 3h7l8 10-8 10h-7l8-10z" fill="#e30613"/></svg>Power tools</li>
        <li><svg viewBox="0 0 26 26"><path d="M1 3h7l8 10-8 10H1l8-10z M11 3h7l8 10-8 10h-7l8-10z" fill="#e30613"/></svg>Delivery &amp; Install available</li>
        <li><svg viewBox="0 0 26 26"><path d="M1 3h7l8 10-8 10H1l8-10z M11 3h7l8 10-8 10h-7l8-10z" fill="#e30613"/></svg>Most vehicles</li>
      </ul>
      <p class="warranty">*product warranty 6 month shelf life battery/1 year blems battery</p>
      <div class="contact">
        <p class="contact__name">DALE MORRICK</p>
        <p class="contact__phone">501-738-2054</p>
        <p class="contact__hours">Monday-Saturday 9-6pm</p>
      </div>
    </section>
  </div>
</body>
</html>
```